Detail Shop Business card design

i need a business card design for my new detailing company called 'Brisk's Polish Works'. i want an all black and white design . simple, direct and to the point. i want the designer to choose a fitting font to match the logothe front should have logo, address, phone and email and the back side should have a slogan and text indicating that we offer services on anything including cars, trucks, motorcycles and RVs. slogan will read "we take pride in your ride"
maybe also very small on the back side the IG icon with Brisks_Polish_Works

phone 208.417.6352
address 3847 E Larkin Ave
Spokane WA 99214
email: BrisksPolish@mailvexo.com

Target Market(s)

all ages , auto enthusiasts

Industry/Entity Type

Automotive

Contact Information for Business Card

the front should have logo, address, phone and email and the back side should have a slogan and text indicating that we offer services on anything including cars, trucks, motorcycles and RVs. slogan will read "we take pride in your ride"

phone 208.417.6352
address 3847 E Larkin Ave
Spokane WA 99214

Colors
000000
ffffff

Requirements
Must have
• bold font and very simple design with good spacing
Nice to have
• anything creative from the designer indicating we service any types of vehicles
Should not have
• any colors ,

```html
<!DOCTYPE html>
<html lang="en">
<head>
<meta charset="utf-8">
<title>Brisk's Polish Works – Business Card</title>
<link rel="stylesheet" href="https://fonts.googleapis.com/css2?family=Oswald:wght@400;500;700&display=swap">
<style>
  :root {
    --ink: #000000;
    --paper: #ffffff;
    --stage: #ffffff;
    --shadow: rgba(0, 0, 0, 0.28);
  }
  * { margin: 0; padding: 0; box-sizing: border-box; }
  html, body {
    width: 1200px; height: 566px; overflow: hidden;
    background: var(--stage);
    font-family: "Oswald", "Arial Narrow", sans-serif;
    color: var(--ink);
  }
  .canvas { position: relative; width: 1200px; height: 566px; }
  .card {
    position: absolute; top: 135px;
    width: 517px; height: 295px;
    background: var(--paper);
    box-shadow: 0 8px 22px var(--shadow);
    overflow: hidden;
  }
  .card--back { left: 67px; }
  .card--front { left: 617px; }

  .slogan {
    font-weight: 700; text-transform: uppercase;
    line-height: 0.98; letter-spacing: 0.2px;
  }
  .services { font-weight: 500; font-size: 13px; line-height: 1.3; }

  .card--back .slogan { position: absolute; left: 79px; top: 96px; font-size: 31px; }
  .card--back .services { position: absolute; left: 79px; top: 166px; }

  .card--front .slogan {
    position: absolute; right: 39px; top: 26px;
    font-size: 34px; text-align: right;
  }
  .card--front .services {
    position: absolute; right: 39px; top: 100px; text-align: right;
  }

  .brand-name {
    position: absolute; width: 190px;
    font-weight: 700; font-size: 36px; line-height: 1.02;
    text-transform: uppercase; text-align: center;
  }
  .card--back .brand-name { left: 318px; top: 90px; }
  .card--front .brand-name { left: 22px; top: 90px; }

  .contact-list {
    position: absolute; right: 38px; top: 160px;
    list-style: none; font-size: 13px; font-weight: 400;
  }
  .contact-item {
    display: flex; justify-content: flex-end; align-items: flex-start;
    gap: 12px; height: 25.5px; text-align: right; line-height: 1.3;
  }
  .contact-item svg { width: 13px; height: 13px; margin-top: 2px; flex: none; }
</style>
</head>
<body>
<main class="canvas">

  <section class="card card--back" aria-label="Card back">
    <h2 class="slogan">We take pride<br>in your ride</h2>
    <p class="services">We offer services on anything including<br>cars, trucks, motorcycles and RVs.</p>
    <p class="brand-name">Brisk's<br>Polish<br>Works</p>
  </section>

  <section class="card card--front" aria-label="Card front">
    <p class="brand-name">Brisk's<br>Polish<br>Works</p>
    <h2 class="slogan">We take pride<br>in your ride</h2>
    <p class="services">We offer services on anything including<br>cars, trucks, motorcycles and RVs.</p>

    <ul class="contact-list">
      <li class="contact-item">
        <span>208.417.6352</span>
        <svg viewBox="0 0 24 24" aria-hidden="true"><path fill="currentColor" d="M6.6 10.8a15.1 15.1 0 0 0 6.6 6.6l2.2-2.2a1 1 0 0 1 1-.25 11.4 11.4 0 0 0 3.6.57 1 1 0 0 1 1 1V20a1 1 0 0 1-1 1A17 17 0 0 1 3 4a1 1 0 0 1 1-1h3.5a1 1 0 0 1 1 1c0 1.25.2 2.45.57 3.57a1 1 0 0 1-.25 1z"/></svg>
      </li>
      <li class="contact-item">
        <span>BrisksPolish@mailvexo.com</span>
        <svg viewBox="0 0 24 24" aria-hidden="true"><path fill="currentColor" d="M2 5h20v14H2z"/><path fill="none" stroke="#fff" stroke-width="1.8" d="M2.5 5.8 12 13l9.5-7.2M2.5 18.2 9 11.5m12.5 6.7L15 11.5"/></svg>
      </li>
      <li class="contact-item">
        <span>Brisks_Polish_Works</span>
        <svg viewBox="0 0 24 24" aria-hidden="true"><rect x="3" y="3" width="18" height="18" rx="5" fill="none" stroke="currentColor" stroke-width="2.2"/><circle cx="12" cy="12" r="4" fill="none" stroke="currentColor" stroke-width="2.2"/></svg>
      </li>
      <li class="contact-item">
        <span>3847 E Larkin Ave<br>Spokane WA 99214</span>
        <svg viewBox="0 0 24 24" aria-hidden="true"><path fill="currentColor" d="M12 2a7 7 0 0 0-7 7c0 5.2 7 13 7 13s7-7.8 7-13a7 7 0 0 0-7-7zm0 9.5A2.5 2.5 0 1 1 12 6.5a2.5 2.5 0 0 1 0 5z"/></svg>
      </li>
    </ul>
  </section>

</main>
</body>
</html>
```